deceased estate clean ups brochures

we would like a brochure to reresent our business we already have new web site and want to do DL A4 brochure to give out to promote our business we already have logo www.brightmoor.com.au is where you can get all info needed

Target Market(s)

families with loved ones that have past away
people done sizing or needing to decluter

Colors
cadf82
33b8a4
886aae
33a6d7

```html
<!DOCTYPE html>
<html lang="en">
<head>
<meta charset="utf-8">
<title>Brightmoor – Deceased Estate Clean Ups Brochure (Outside)</title>
<link href="https://fonts.googleapis.com/css2?family=Cinzel:wght@400;700&family=Open+Sans:ital,wght@0,400;0,600;0,700;1,400&display=swap" rel="stylesheet">
<style>
  :root{
    --green:#8dc63f;
    --green-dark:#6fa82a;
    --ink:#1e1e1e;
    --charcoal:#2c2c2c;
    --paper:#f4f4f4;
    --text:#333;
    --blue:#1c8ed1;
    --stage:#3a3a3a;
  }
  html,body{margin:0;padding:0;width:802px;height:1200px;overflow:hidden;background:var(--stage);}
  .brochure{position:absolute;left:21px;top:302px;width:760px;height:596px;background:var(--paper);
    box-shadow:0 8px 24px rgba(0,0,0,.45);overflow:hidden;font-family:"Open Sans",Arial,sans-serif;color:var(--text);}
  .brochure__art{position:absolute;inset:0;}
  .panel{position:absolute;top:0;width:253px;height:596px;text-align:center;}
  .panel--left{left:0}
  .panel--middle{left:253px}
  .panel--cover{left:507px}
  .serif{font-family:"Cinzel",Georgia,serif;}
  .footer-url{position:absolute;left:0;right:0;bottom:0;height:26px;line-height:26px;font-size:8.5px;letter-spacing:.6px;}
  .footer-url--dark{color:var(--green)}
  .footer-url--green{color:var(--ink)}

  /* left panel */
  .why-title{position:absolute;top:31px;left:0;right:0;font-size:12.5px;font-weight:700;color:var(--ink);}
  .why-title span{color:var(--green)}
  .feature{position:absolute;left:20px;right:14px;}
  .feature__icon{display:block;margin:0 auto 3px;width:20px;height:20px;}
  .feature__title{font-size:8.6px;font-weight:700;color:var(--ink);margin:0 0 3px;}
  .feature__text{font-size:6.6px;line-height:9.6px;margin:0;}

  /* middle panel */
  .quote{position:absolute;top:236px;left:18px;right:20px;height:66px;border:1px dashed #bdbdbd;border-radius:10px;}
  .quote__text{margin:10px 8px 0;font-size:6.9px;line-height:10.6px;font-style:italic;}
  .quote__mark{position:absolute;top:212px;left:0;right:0;font-family:Georgia,serif;font-size:56px;line-height:40px;color:#c8c8c8;font-weight:700;}
  .quote__author{position:absolute;top:309px;left:0;right:0;font-size:11px;font-weight:700;color:var(--blue);letter-spacing:.3px;}
  .quote__author small{font-size:5.6px;color:var(--ink);font-weight:400;letter-spacing:.2px;}
  .brand{display:flex;align-items:center;justify-content:center;gap:6px;color:var(--ink);}
  .brand__dot{width:12px;height:12px;border-radius:50%;background:var(--green);}
  .brand--small{position:absolute;top:392px;left:0;right:0;font-size:13.5px;}
  .enquire{position:absolute;top:418px;left:0;right:0;font-size:8.4px;line-height:14px;}
  .enquire strong{color:var(--green);font-size:11px;font-weight:600;}
  .enquire b{color:var(--ink);font-size:11px;font-weight:600;}
  .contact-icons{position:absolute;top:466px;left:0;right:0;display:flex;justify-content:center;gap:7px;}
  .contact-icons svg{width:15px;height:15px;}
  .contact{position:absolute;top:493px;left:0;right:0;font-size:8.8px;line-height:11.6px;color:var(--ink);}

  /* cover panel */
  .brand--cover{position:absolute;top:88px;left:0;right:0;font-size:23px;letter-spacing:1px;}
  .brand--cover .brand__dot{width:18px;height:18px;}
  .cover-kicker{position:absolute;top:421px;left:0;right:0;font-size:11.5px;color:var(--green);letter-spacing:.6px;}
  .cover-title{position:absolute;top:443px;left:0;right:0;margin:0;font-weight:400;color:var(--ink);line-height:1;}
  .cover-title .line1{display:block;font-size:21px;letter-spacing:.5px;}
  .cover-title .line2{display:block;font-size:34px;margin-top:3px;letter-spacing:.5px;}
  .cover-text{position:absolute;top:512px;left:22px;right:22px;margin:0;font-size:7.6px;line-height:11.4px;}
</style>
</head>
<body>
<main class="brochure">
  <svg class="brochure__art" viewBox="0 0 760 596" width="760" height="596" aria-hidden="false">
    <rect width="760" height="596" fill="#f4f4f4"/>
    <!-- left panel top band -->
    <path d="M0 0H253V20C180 30 80 48 0 60Z" fill="#1e1e1e"/>
    <path d="M0 64C80 52 180 34 253 25" fill="none" stroke="#8dc63f" stroke-width="3"/>
    <!-- left panel photo -->
    <rect x="0" y="385" width="253" height="186" fill="#c9c2b6" role="img" aria-label="Photo: consultant shaking hands with an elderly client at home"/>
    <rect x="0" y="385" width="253" height="186" fill="url(#leftPhoto)"/>
    <path d="M0 380H253V388C190 410 90 424 0 408Z" fill="#f4f4f4"/>
    <path d="M0 410C90 426 190 412 253 390" fill="none" stroke="#8dc63f" stroke-width="3"/>
    <!-- middle + cover top dark -->
    <path d="M253 0H760V140L253 80Z" fill="#1e1e1e"/>
    <path d="M253 80C330 95 400 100 470 110L507 116V0H253Z" fill="#1e1e1e"/>
    <!-- middle circle photo -->
    <circle cx="380" cy="148" r="84" fill="#2c2c2c"/>
    <circle cx="380" cy="148" r="72" fill="url(#circlePhoto)" role="img" aria-label="Photo: smiling elderly couple seated on a garden bench"/>
    <!-- cover photo -->
    <rect x="507" y="120" width="253" height="290" fill="url(#coverPhoto)" role="img" aria-label="Photo: removalists in blue uniforms carrying cardboard boxes"/>
    <!-- cover white top shape -->
    <path d="M522 0H760V108C700 138 610 138 565 112C535 92 522 50 522 0Z" fill="#f7f7f7"/>
    <path d="M562 130C620 150 700 144 760 118" fill="none" stroke="#8dc63f" stroke-width="4"/>
    <path d="M507 138C540 150 560 150 580 148" fill="none" stroke="#1e1e1e" stroke-width="0"/>
    <!-- cover bottom white shape -->
    <path d="M507 402C600 378 690 390 760 350V596H507Z" fill="#f4f4f4"/>
    <path d="M507 398C600 372 690 384 760 344" fill="none" stroke="#8dc63f" stroke-width="4"/>
    <path d="M507 408C600 386 690 398 760 360" fill="none" stroke="#cfcfcf" stroke-width="2"/>
    <!-- footers -->
    <rect x="0" y="570" width="253" height="26" fill="#1e1e1e"/>
    <rect x="253" y="570" width="254" height="26" fill="#8dc63f"/>
    <rect x="507" y="570" width="253" height="26" fill="#1e1e1e"/>
    <defs>
      <linearGradient id="leftPhoto" x1="0" y1="0" x2="1" y2="1">
        <stop offset="0" stop-color="#e8e4dc"/><stop offset=".5" stop-color="#cfc6b8"/><stop offset="1" stop-color="#9e9282"/>
      </linearGradient>
      <linearGradient id="circlePhoto" x1="0" y1="0" x2="1" y2="1">
        <stop offset="0" stop-color="#b36a52"/><stop offset=".5" stop-color="#d9d6d2"/><stop offset="1" stop-color="#6f8a58"/>
      </linearGradient>
      <linearGradient id="coverPhoto" x1="0" y1="0" x2="1" y2="1">
        <stop offset="0" stop-color="#a8c4de"/><stop offset=".45" stop-color="#b89772"/><stop offset="1" stop-color="#2f4d86"/>
      </linearGradient>
    </defs>
  </svg>

  <!-- LEFT PANEL -->
  <section class="panel panel--left">
    <h2 class="why-title serif">Why <span>Choose Us</span></h2>

    <div class="feature" style="top:66px">
      <svg class="feature__icon" viewBox="0 0 20 20"><circle cx="10" cy="10" r="10" fill="var(--green)"/><path d="M5.5 10.3l3 3 6-6.5" fill="none" stroke="#fff" stroke-width="2"/></svg>
      <h3 class="feature__title">QUALITY</h3>
      <p class="feature__text">Our goal is to enhance your property and achieve the results you are looking for. We appreciate the trust placed in us to deliver a quality job that meets your expectations...</p>
    </div>

    <div class="feature" style="top:148px">
      <svg class="feature__icon" viewBox="0 0 20 20"><circle cx="10" cy="10" r="10" fill="var(--green)"/><rect x="5" y="7.5" width="10" height="7" rx="1" fill="#fff"/><rect x="8" y="5.5" width="4" height="2.5" fill="none" stroke="#fff" stroke-width="1.2"/></svg>
      <h3 class="feature__title">PROFESSIONALISM</h3>
      <p class="feature__text">Brightmoor only use quality staff and materials that are "fit for purpose". We keep a professional approach to every job ensuring all agreed tasks are completed and accounted...</p>
    </div>

    <div class="feature" style="top:232px">
      <svg class="feature__icon" viewBox="0 0 20 20"><circle cx="10" cy="10" r="10" fill="var(--green)"/><path d="M10 15l-4.5-4.3a2.6 2.6 0 0 1 4.5-3 2.6 2.6 0 0 1 4.5 3Z" fill="#fff"/></svg>
      <h3 class="feature__title">PRIDE</h3>
      <p class="feature__text">We take pride in our family approach and care we bring to your loved ones belongings. Whether it is simple house clearing, house repairs or larger renovations your...</p>
    </div>

    <div class="feature" style="top:314px">
      <svg class="feature__icon" viewBox="0 0 20 20"><path d="M10 1a6 6 0 0 0-6 6c0 4.5 6 11 6 11s6-6.5 6-11a6 6 0 0 0-6-6z" fill="var(--green)"/><circle cx="10" cy="7" r="2.3" fill="#fff"/></svg>
      <h3 class="feature__title">AREAS SERVICED</h3>
      <p class="feature__text">Specialising in Melbourne CBD and suburbs including: Coburg, Falkner, Campbellfield, Craigieburn, St. Kilda, Brighton, Caulfield, Hawthorn, Heidelberg, Watsonia...</p>
    </div>

    <div class="footer-url footer-url--dark">www.brightmoor.com.au</div>
  </section>

  <!-- MIDDLE PANEL -->
  <section class="panel panel--middle">
    <div class="quote__mark">&ldquo;</div>
    <div class="quote"><p class="quote__text">Check out Brightmoor if you are in need of home, building, and storage units clean out services that will suit your needs. They also handle estate sales and are always available on time.</p></div>
    <div class="quote__author">DANIEL <small>CUSTOMER</small></div>

    <div class="brand brand--small serif"><span class="brand__dot"></span>BRIGHTMOOR</div>
    <p class="enquire" style="margin:0">If you have any queries,<br><strong>Get in touch</strong> <b>with us</b></p>

    <div class="contact-icons">
      <svg viewBox="0 0 16 16"><circle cx="8" cy="8" r="8" fill="var(--green)"/><path d="M8 3.5a3 3 0 0 0-3 3c0 2.3 3 6 3 6s3-3.7 3-6a3 3 0 0 0-3-3z" fill="#fff"/><circle cx="8" cy="6.5" r="1.1" fill="var(--green)"/></svg>
      <svg viewBox="0 0 16 16"><circle cx="8" cy="8" r="8" fill="var(--green)"/><path d="M5.5 4l1.6 2-1 1c.6 1.3 1.5 2.2 2.8 2.8l1-1 2 1.6-1 1.5C7.8 12 4 8.2 4 5z" fill="#fff"/></svg>
      <svg viewBox="0 0 16 16"><circle cx="8" cy="8" r="8" fill="var(--green)"/><rect x="5.5" y="4" width="5" height="2.5" fill="#fff"/><rect x="4" y="6.5" width="8" height="4" rx=".8" fill="#fff"/><rect x="5.5" y="9.5" width="5" height="2.5" fill="#fff" stroke="var(--green)" stroke-width=".6"/></svg>
      <svg viewBox="0 0 16 16"><circle cx="8" cy="8" r="8" fill="var(--green)"/><circle cx="8" cy="8" r="4.2" fill="none" stroke="#fff" stroke-width="1"/><ellipse cx="8" cy="8" rx="1.8" ry="4.2" fill="none" stroke="#fff" stroke-width="1"/><path d="M3.8 8h8.4" stroke="#fff" stroke-width="1"/></svg>
    </div>

    <p class="contact" style="margin:0">PO Box 120, Northvale 3999<br>0400 318 642<br>0400 318 642<br>info@brightmoor.com.au</p>

    <div class="footer-url footer-url--green">www.brightmoor.com.au</div>
  </section>

  <!-- COVER PANEL -->
  <section class="panel panel--cover">
    <div class="brand brand--cover serif"><span class="brand__dot"></span>BRIGHTMOOR</div>
    <div class="cover-kicker">WE'RE HERE TO HELP</div>
    <h1 class="cover-title serif"><span class="line1">DECEASED ESTATE</span><span class="line2">CLEAN UPS</span></h1>
    <p class="cover-text">At Brightmoor our goal is to ease your worries and help you with your journey in preparing your house for rental or resale.</p>
    <div class="footer-url footer-url--dark">www.brightmoor.com.au</div>
  </section>
</main>
</body>
</html>
```